Coastline Premier Retreats Business Card Design

Design a business card for Coastline Premier Retreats. Look at the website for colors and reference. Card should have logo, name, title, office number, mobile number, email, URL and a tagline like, "Luxury Hotel & Resort Email Marketing" (This might change).

https://www.coastlinepremierretreats.example

The rest I will leave up to your imagination.

Contact Information for Business Card

Logo, name, title, office number, mobile number, email, URL and a tagline like, "Luxury Hotel & Resort Email Marketing" (This might change).

```html
<!DOCTYPE html>
<html lang="en">
<head>
<meta charset="utf-8">
<title>Coastline Premier Retreats – Business Card</title>
<link href="https://fonts.googleapis.com/css2?family=Montserrat:ital,wght@0,400;0,700;0,800;1,400&display=swap" rel="stylesheet">
<style>
  :root {
    --backdrop: #2a2a2a;
    --card: #1a1a1a;
    --orange: #f47a1f;
    --white: #f2f2f2;
    --muted: #3a3a3a;
  }
  * { margin: 0; padding: 0; box-sizing: border-box; }
  html, body { width: 1200px; height: 900px; overflow: hidden; }
  body {
    background: var(--backdrop);
    font-family: "Montserrat", Arial, sans-serif;
    color: var(--white);
    display: flex;
    flex-direction: column;
    align-items: center;
    justify-content: center;
    gap: 40px;
  }
  .card {
    width: 700px;
    height: 400px;
    background: var(--card);
    position: relative;
    box-shadow: 0 12px 30px rgba(0,0,0,.5);
  }

  /* Front */
  .brand {
    position: absolute;
    left: 56px;
    top: 120px;
    width: 250px;
    display: flex;
    align-items: center;
    gap: 12px;
  }
  .brand-square { width: 16px; height: 16px; background: var(--orange); flex: none; }
  .brand-name {
    font-weight: 800;
    font-size: 22px;
    line-height: 1.15;
    text-transform: uppercase;
    color: var(--white);
  }
  .divider {
    position: absolute;
    left: 330px;
    top: 70px;
    width: 1px;
    height: 230px;
    background: var(--orange);
    transform: rotate(14deg);
  }
  .person {
    position: absolute;
    left: 370px;
    top: 82px;
  }
  .person-name {
    font-weight: 800;
    font-size: 30px;
    color: var(--orange);
    text-transform: uppercase;
    letter-spacing: .5px;
  }
  .person-title { font-size: 15px; margin-top: 2px; }
  .contacts { list-style: none; margin-top: 24px; }
  .contacts li {
    display: flex;
    align-items: center;
    gap: 10px;
    font-size: 15px;
    line-height: 26px;
  }
  .contacts svg { width: 14px; height: 14px; fill: var(--orange); flex: none; }
  .highlight { color: var(--orange); }
  .address {
    position: absolute;
    left: 56px;
    bottom: 44px;
    font-size: 15px;
  }

  /* Back */
  .back-name {
    position: absolute;
    left: 0; right: 0;
    top: 120px;
    text-align: center;
    font-weight: 800;
    font-size: 52px;
    line-height: 1.05;
    text-transform: uppercase;
    color: var(--muted);
  }
  .tagline {
    position: absolute;
    left: 0; right: 0;
    top: 290px;
    text-align: center;
    font-style: italic;
    font-size: 22px;
    color: var(--orange);
  }
</style>
</head>
<body>

  <section class="card card-front">
    <div class="brand">
      <span class="brand-square"></span>
      <span class="brand-name">Coastline Premier Retreats</span>
    </div>
    <div class="divider"></div>
    <div class="person">
      <h1 class="person-name">Marcus Delaney</h1>
      <p class="person-title">CEO/Founder</p>
      <ul class="contacts">
        <li>
          <svg viewBox="0 0 16 16" aria-hidden="true"><path d="M4 1h8v14H4z M5.5 2.5v9h5v-9z M7 13h2v1H7z" fill-rule="evenodd"/></svg>
          555.014.2270
        </li>
        <li>
          <svg viewBox="0 0 16 16" aria-hidden="true"><path d="M1 6c0-2 3-4 7-4s7 2 7 4v1h-4V5H5v2H1z M3 9h10l1 6H2z"/></svg>
          +34 600 555 012
        </li>
        <li>
          <svg viewBox="0 0 16 16" aria-hidden="true"><path d="M1 3h14v10H1z M2 4l6 5 6-5" fill-rule="evenodd"/></svg>
          info@coastlinepremierretreats.example
        </li>
        <li>
          <svg viewBox="0 0 16 16" aria-hidden="true"><circle cx="8" cy="8" r="7"/></svg>
          <span>www.<span class="highlight">coastlinepremierretreats</span>.example</span>
        </li>
      </ul>
    </div>
    <p class="address">Po Box, 48 Harbor Lane Bayview, AB 00000</p>
  </section>

  <section class="card card-back">
    <p class="back-name">Coastline<br>Premier Retreats</p>
    <p class="tagline">Luxury Hotel &amp; Resort Email Marketing</p>
  </section>

</body>
</html>
```